Dalvick's Business Card

I need some designs for a new business card including the new logo attached. An old example of our business card is also attached to show all the data that should be included on the new design.
**I added some more examples someone had mocked up**

Contact Information for Business Card

Should include all info on other examples uploaded.

```html
<!DOCTYPE html>
<html lang="en">
<head>
<meta charset="UTF-8">
<title>Dalvick's Business Card</title>
<link href="https://fonts.googleapis.com/css2?family=Bebas+Neue&family=Poppins:wght@400;600;700&display=swap" rel="stylesheet">
<style>
  :root {
    --brand-red: #ec1c24;
    --brand-blue: #0070c0;
    --paper: #ffffff;
    --ink: #1a1a1a;
    --stage: #2a2a2a;
  }
  * { box-sizing: border-box; margin: 0; padding: 0; }
  html, body { width: 1200px; height: 1015px; overflow: hidden; }
  body {
    background: var(--stage);
    font-family: 'Poppins', sans-serif;
    position: relative;
  }
  .card {
    position: absolute;
    width: 560px;
    height: 320px;
    overflow: hidden;
  }
  /* Front */
  .card-front { left: 60px; top: 120px; background: var(--brand-blue); }
  .card-front .red-field { position: absolute; inset: 0; }
  .front-name {
    position: absolute; left: 30px; top: 126px;
    font-family: 'Poppins', sans-serif; font-weight: 700;
    font-size: 34px; color: var(--paper);
  }
  .front-copy {
    position: absolute; left: 300px; top: 40px; width: 236px;
    color: var(--paper); text-align: left;
  }
  .headline {
    font-family: 'Bebas Neue', sans-serif;
    font-size: 36px; line-height: 1.0; letter-spacing: 0.5px;
  }
  .rule { height: 1px; background: var(--paper); margin: 16px 0 12px; width: 230px; }
  .service-area { font-weight: 600; font-size: 17px; line-height: 1.2; }

  /* Back */
  .card-back { left: 580px; top: 560px; background: var(--paper); }
  .back-brand {
    position: absolute; left: 40px; top: 128px;
    display: flex; align-items: center; gap: 10px;
  }
  .brand-dot { width: 22px; height: 22px; border-radius: 50%; background: var(--brand-red); }
  .brand-name { font-weight: 700; font-size: 34px; color: var(--brand-blue); letter-spacing: 0.5px; }
  .divider { position: absolute; left: 268px; top: 70px; width: 1px; height: 110px; background: #9cc3e4; }
  .contact { position: absolute; left: 292px; top: 76px; }
  .person { color: var(--brand-blue); font-weight: 600; font-size: 24px; letter-spacing: 0.5px; margin-bottom: 12px; }
  .contact-row { display: flex; align-items: center; gap: 10px; font-size: 15px; color: var(--ink); margin-bottom: 6px; }
  .contact-row svg { width: 18px; height: 18px; }
  .bands { position: absolute; left: 0; bottom: 0; width: 100%; height: 66px; }
  .band-text {
    position: absolute; bottom: 0;
    display: flex; align-items: center; justify-content: center;
    color: var(--paper); font-weight: 700;
    font-size: 14px; letter-spacing: 0.5px; white-space: nowrap;
  }
  .band-licensed { left: 0; width: 316px; height: 38px; }
  .band-family { left: 330px; right: 0; height: 66px; }
</style>
</head>
<body>

<section class="card card-front">
  <svg class="red-field" viewBox="0 0 560 320" preserveAspectRatio="none">
    <polygon points="0,0 150,0 260,320 0,320" fill="var(--brand-red)"/>
  </svg>
  <div class="front-name">Dalvick's</div>
  <div class="front-copy">
    <p class="headline">Call today for<br>all your HVAC,<br>refrigeration &amp;<br>plumbing needs</p>
    <div class="rule"></div>
    <p class="service-area">Serves Fairbrook<br>IA &amp; Surrounding<br>Areas</p>
  </div>
</section>

<section class="card card-back">
  <div class="back-brand">
    <span class="brand-dot"></span>
    <span class="brand-name">DALVICK'S</span>
  </div>
  <div class="divider"></div>
  <div class="contact">
    <p class="person">GLEN DALVICK</p>
    <p class="contact-row">
      <svg viewBox="0 0 24 24"><path d="M6.6 10.8a15.1 15.1 0 0 0 6.6 6.6l2.2-2.2a1 1 0 0 1 1-.25 11.4 11.4 0 0 0 3.6.57 1 1 0 0 1 1 1V20a1 1 0 0 1-1 1A17 17 0 0 1 3 4a1 1 0 0 1 1-1h3.5a1 1 0 0 1 1 1c0 1.250.2 2.450.57 3.57a1 1 0 0 1-.25 1z" fill="var(--brand-red)"/></svg>
      555.014.2290
    </p>
    <p class="contact-row">
      <svg viewBox="0 0 24 24"><rect x="2" y="5" width="20" height="14" fill="var(--brand-red)"/><path d="M2 5l10 8 10-8" fill="none" stroke="#fff" stroke-width="1.6"/></svg>
      hvacdalvick@mailbox.com
    </p>
  </div>
  <svg class="bands" viewBox="0 0 560 66" preserveAspectRatio="none">
    <rect x="0" y="28" width="330" height="38" fill="var(--brand-red)"/>
    <polygon points="316,0 560,0 560,66 324,66" fill="var(--brand-blue)"/>
  </svg>
  <span class="band-text band-licensed">LICENSED &amp; INSURED</span>
  <span class="band-text band-family">FAMILY OWNED &amp; OPERATED</span>
</section>

</body>
</html>
```